TV Antenna Installation business needs a unique flyer

We need a simple but effective flyer design for our TV Aerial installation company based in Newcastle, NSW, Australia called Bright Harbour TV & Aerial Svcs.
We are trying to target areas where there has been a new transmitter installed and most houses just require their aerial redirecting and tv's retuning.

Industry/Entity Type

Business

Requirements
Must have
• We would like the idea of a headline phrase such as " Poor TV reception……..now a thing from the past" or something similar & catchy.
Also "Did you know a new transmitter has been recently installed in your area, we can therefore now GUARANTEE 100% PERFECT PICTURE
Charges from only $95.
- Free 5 year warranty
- Free signal testing
- Free Onsite Quote
Phone 0463 527 209
Nice to have
• Other services include:

- New Installs
- Extra Points & repairs
- TV wall mounting/Home Cinema
- Pull down tall masts

Modern tv picture, see example uploaded

```html
<!DOCTYPE html>
<html lang="en">
<head>
<meta charset="utf-8">
<title>Bright Harbour TV &amp; Aerial Svcs – Flyer</title>
<link href="https://fonts.googleapis.com/css2?family=Arimo:wght@700&family=Archivo+Black&family=Sniglet:wght@800&display=swap" rel="stylesheet">
<style>
  :root{
    --paper:#e1f1fa;
    --navy:#25338f;
    --navy-deep:#1b2277;
    --red:#b01e2e;
    --red-bright:#e8212b;
    --yellow:#fff200;
    --green:#0b6b2c;
    --teal:#1ba6cf;
    --lime:#b5d334;
    --screen:#1fa6d6;
    --white:#ffffff;
  }
  *{margin:0;padding:0;box-sizing:border-box}
  html,body{width:871px;height:1200px;overflow:hidden;background:var(--paper)}
  .flyer{position:relative;width:871px;height:1200px;background:var(--paper);overflow:hidden;font-family:"Arimo",Arial,sans-serif;font-weight:700}
  .decor{position:absolute;inset:0;width:871px;height:1200px}
  .brand{position:absolute;left:50px;top:40px;font-size:54px;font-weight:700;color:var(--yellow);letter-spacing:0.5px}
  .headline{position:absolute;font-family:"Sniglet",cursive;font-weight:800;color:var(--green);-webkit-text-stroke:8px var(--white);paint-order:stroke fill;line-height:1;white-space:nowrap}
  .headline--main{left:50px;top:198px;font-size:92px}
  .headline--sub{left:92px;top:298px;font-size:44px}
  .headline--past{left:58px;top:388px;font-size:44px;line-height:50px}
  .tv-art{position:absolute;left:450px;top:60px;width:380px;height:520px;background:radial-gradient(ellipse at 50% 55%,var(--screen) 0%,#4cc0e6 40%,rgba(225,241,250,0) 70%)}
  .pitch{position:absolute;left:48px;top:528px;width:320px;font-size:29px;line-height:37.5px;color:var(--navy)}
  .guarantee{position:absolute;left:48px;top:716px;font-size:35px;line-height:42px;color:var(--red);white-space:nowrap}
  .perks{position:absolute;left:433px;top:593px;list-style:none}
  .perks li{height:62px;white-space:nowrap;color:var(--green);font-family:"Archivo Black",sans-serif;font-weight:400;font-size:30px}
  .perks .free{color:var(--red);font-size:42px;margin-right:6px}
  .services-title{position:absolute;left:417px;top:830px;font-size:36px;color:var(--teal)}
  .services{position:absolute;left:417px;top:880px;list-style:none}
  .services li{height:37.5px;display:flex;align-items:center;font-size:24px;color:var(--navy);white-space:nowrap}
  .services svg{width:24px;height:22px;margin-right:12px;flex:none}
  .price{position:absolute;left:40px;top:866px;width:338px;height:216px;border-radius:50%;background:radial-gradient(ellipse at 50% 40%,#c2182a,#8e0f1c);border:6px solid var(--red-bright);text-align:center;color:var(--white);padding-top:30px}
  .price p{font-size:36px;line-height:42px}
  .price strong{display:block;font-family:"Archivo Black",sans-serif;font-weight:400;font-size:64px;line-height:76px;color:var(--yellow)}
  .phone{position:absolute;right:28px;top:1125px;display:flex;align-items:center;font-size:50px;color:var(--yellow)}
  .phone svg{width:40px;height:40px;margin-right:8px}
</style>
</head>
<body>
<div class="flyer">
  <svg class="decor" viewBox="0 0 871 1200" aria-hidden="true">
    <defs>
      <linearGradient id="navyBand" x1="0" x2="1">
        <stop offset="0" stop-color="#25338f"/><stop offset="1" stop-color="#1b2277"/>
      </linearGradient>
    </defs>
    <path d="M0 0H785C600 85 320 128 0 122Z" fill="url(#navyBand)"/>
    <path d="M0 128C310 138 520 104 685 48C540 115 300 162 0 160Z" fill="#b01e2e"/>
    <path d="M0 1084C220 1136 460 1118 660 1040C470 1128 220 1150 0 1098Z" fill="#1ba6cf"/>
    <path d="M0 1104C300 1160 600 1140 871 1080V1200H0Z" fill="url(#navyBand)"/>
    <path d="M120 1128C420 1142 660 1094 871 1046V1068C660 1112 420 1146 120 1128Z" fill="#b5d334"/>
    <path d="M160 1138C460 1146 700 1110 871 1076V1092C700 1124 460 1150 160 1138Z" fill="#b01e2e"/>
  </svg>

  <div class="brand">Bright Harbour</div>

  <div class="headline headline--main">Poor TV</div>
  <div class="headline headline--sub">reception.......</div>
  <div class="headline headline--past">now a thing<br>from the past</div>

  <div class="tv-art" role="img" aria-label="Illustration of a retro television with an antenna and a red no-entry sign on the screen"></div>

  <p class="pitch">Did you know a new transmitter has been recently installed in your area, we can therefore now</p>
  <p class="guarantee">GUARANTEE 100%<br>PERFECT PICTURE</p>

  <ul class="perks">
    <li><span class="free">Free</span>5 year warranty</li>
    <li><span class="free">Free</span>signal testing</li>
    <li><span class="free">Free</span>Onsite Quote</li>
  </ul>

  <h2 class="services-title">Our services</h2>
  <ul class="services">
    <li><svg viewBox="0 0 24 22"><rect x="1" y="5" width="16" height="15" fill="none" stroke="#25338f" stroke-width="2"/><path d="M4 11l5 5L22 2" fill="none" stroke="#e8212b" stroke-width="3"/></svg>New Installs</li>
    <li><svg viewBox="0 0 24 22"><rect x="1" y="5" width="16" height="15" fill="none" stroke="#25338f" stroke-width="2"/><path d="M4 11l5 5L22 2" fill="none" stroke="#e8212b" stroke-width="3"/></svg>Extra Points &amp; repairs</li>
    <li><svg viewBox="0 0 24 22"><rect x="1" y="5" width="16" height="15" fill="none" stroke="#25338f" stroke-width="2"/><path d="M4 11l5 5L22 2" fill="none" stroke="#e8212b" stroke-width="3"/></svg>TV wall mounting/Home Cinema</li>
    <li><svg viewBox="0 0 24 22"><rect x="1" y="5" width="16" height="15" fill="none" stroke="#25338f" stroke-width="2"/><path d="M4 11l5 5L22 2" fill="none" stroke="#e8212b" stroke-width="3"/></svg>Pull down tall masts</li>
  </ul>

  <div class="price">
    <p>Charges<br>from only</p>
    <strong>$95</strong>
  </div>

  <div class="phone">
    <svg viewBox="0 0 40 40" aria-hidden="true"><circle cx="20" cy="20" r="18" fill="none" stroke="#ffffff" stroke-width="2.5"/><path d="M14 9c-3 2-4 5-2 10 2 6 6 10 11 12 3 1 5 0 6-2l-4-5-3 2c-3-2-5-5-6-8l3-2z" fill="#ffffff"/></svg>
    <span>0463 527 209</span>
  </div>
</div>
</body>
</html>
```